New Business Card Design Project

We require a business card design for Vexalund, a newly established Indian company.
Our focus is on the development, manufacturing, and export of a diverse array of pharmaceutical products on a global scale. The card should convey a professional appearance, as our primary markets are in Africa, China, and Southeast Asian nations.
We envision a two-sided business card, with the reverse side dedicated to a logo set against a solid color or an elegantly designed pattern. The corners should be rounded. We would appreciate seeing both horizontal and vertical design options. We trust the designer to utilize their expertise in creating this design.

The content for the business card is included in the attached Word file.

Target Market(s)

Our primary markets are in Africa, China, and Southeast Asian, Latin America, Maldives, Sri Lanka

Industry/Entity Type

Pharmaceutical Manufacturing and Export

Contact Information for Business Card

Colors

Designer to choose colors to be used in the design.

Requirements
Must have
• The reverse side of the business card features solely the logo along with the tagline, "Care for Every Life."
Should not have
• The logo should not exceed two instances, encompassing both the front and back sides of the card.

```html
<!DOCTYPE html>
<html lang="en">
<head>
<meta charset="utf-8">
<title>Vexalund Business Card</title>
<link rel="stylesheet" href="https://fonts.googleapis.com/css2?family=Open+Sans:wght@400;600;700&family=Poppins:wght@400;700&display=swap">
<style>
  :root {
    --bg: #232323;
    --coral: #f0634f;
    --card-dark: #222226;
    --blue: #2fa6df;
    --white: #ffffff;
    --shadow: rgba(0, 0, 0, 0.55);
  }
  * { margin: 0; padding: 0; box-sizing: border-box; }
  html, body {
    width: 1200px; height: 780px; overflow: hidden;
    background: var(--bg);
  }
  .stage {
    position: relative; width: 1200px; height: 780px;
    display: flex; align-items: center; justify-content: center; gap: 40px;
  }
  .card {
    position: relative; width: 540px; height: 310px;
    border-radius: 22px;
    box-shadow: 0 14px 30px var(--shadow);
    overflow: hidden;
  }
  /* Reverse side */
  .card-back {
    background: var(--coral);
    display: flex; flex-direction: column; align-items: center; justify-content: center;
  }
  .brand-back {
    font-family: "Poppins", sans-serif; font-weight: 700;
    font-size: 58px; letter-spacing: 1px; color: var(--white); line-height: 1;
  }
  .tagline {
    margin-top: 18px;
    font-family: "Poppins", sans-serif; font-weight: 400;
    font-size: 14px; letter-spacing: 1px; color: var(--white);
  }
  /* Front side */
  .card-front { background: var(--card-dark); }
  .brand-front {
    position: absolute; right: 36px; top: 92px;
    font-family: "Poppins", sans-serif; font-weight: 700;
    font-size: 46px; letter-spacing: 1px; color: var(--blue); line-height: 1;
  }
  .identity {
    position: absolute; left: 34px; top: 140px;
    padding-left: 14px; border-left: 6px solid var(--blue);
    font-family: "Open Sans", sans-serif; line-height: 1.1;
  }
  .person-first { font-weight: 700; font-size: 24px; color: var(--blue); }
  .person-last { font-weight: 400; font-size: 24px; color: var(--coral); letter-spacing: 1px; }
  .role { font-size: 14px; color: var(--white); margin-top: 2px; }
  .address {
    position: absolute; left: 54px; top: 200px;
    font-family: "Open Sans", sans-serif; font-style: normal;
    font-size: 12.5px; line-height: 1.35;
    color: var(--blue); letter-spacing: 0.5px;
  }
  .contacts {
    position: absolute; left: 54px; top: 238px; list-style: none;
    font-family: "Open Sans", sans-serif; font-size: 12.5px; color: var(--white);
    letter-spacing: 0.4px;
  }
  .contacts li { display: flex; align-items: center; gap: 8px; height: 17px; }
  .contacts svg { width: 12px; height: 12px; flex: none; }
</style>
</head>
<body>
<main class="stage">
  <section class="card card-back" aria-label="Card reverse side">
    <div class="brand-back">Vexalund</div>
    <div class="tagline">Care for Every Life.</div>
  </section>

  <section class="card card-front" aria-label="Card front side">
    <div class="brand-front">Vexalund</div>

    <div class="identity">
      <div><span class="person-first">Ravi</span> <span class="person-last">K. Solanke</span></div>
      <div class="role">CEO</div>
    </div>

    <address class="address">
      12, Kamal Nagar,<br>Nashik, 422001, India
    </address>

    <ul class="contacts">
      <li>
        <svg viewBox="0 0 12 12" aria-hidden="true"><rect x="2.5" y="0.8" width="7" height="10.4" rx="1" fill="none" stroke="#f0634f" stroke-width="1.3"/></svg>
        <span>+91 98450 31762</span>
      </li>
      <li>
        <svg viewBox="0 0 12 12" aria-hidden="true"><circle cx="6" cy="6" r="5" fill="none" stroke="#2fa6df" stroke-width="1.3"/><ellipse cx="6" cy="6" rx="2.2" ry="5" fill="none" stroke="#2fa6df" stroke-width="1"/><line x1="1" y1="6" x2="11" y2="6" stroke="#2fa6df" stroke-width="1"/></svg>
        <span>www.vexalund.com</span>
      </li>
      <li>
        <svg viewBox="0 0 12 12" aria-hidden="true"><rect x="0.8" y="2.5" width="10.4" height="7.5" fill="none" stroke="#f0634f" stroke-width="1.3"/><polyline points="0.8,2.5 6,7 11.2,2.5" fill="none" stroke="#f0634f" stroke-width="1.2"/></svg>
        <span>rsolanke@vexalund.com</span>
      </li>
    </ul>
  </section>
</main>
</body>
</html>
```